Tovimar Community Development Planning New web site

Design a new web site. I have a budget of $1,500.00.
Attached on PowerPoint is a complete site plan. Home page and linked pages.
10 - 12 pages. All copy and photos will be supplied. (300dpi)
I have shown them the concept which they like.
No data bases required. Home page with animations dissolving.
They former web site has been taken down. They have been in business 30 years in New Jersey
Colors teal blues and greens
There will be a new logo)being designed)
The text in home page copy will give you a detailed story what they are all about.

files have been approved for Tovimar, Inc.   Brenton is the designer

```html
<!DOCTYPE html>
<html lang="en">
<head>
<meta charset="utf-8">
<title>Tovimar, Inc. | Community Development Planning</title>
<link href="https://fonts.googleapis.com/css2?family=Roboto+Condensed:wght@400;700&family=Lato:wght@400;700&display=swap" rel="stylesheet">
<style>
:root{
  --sky:#5bb8f5;
  --blue:#1591e3;
  --blue-deep:#0f85dc;
  --link:#1a86d8;
  --ink:#3c3c3c;
  --muted:#555;
  --faint:#b5b5b5;
  --line:#e2e2e2;
  --panel-top:#f6f6f6;
  --panel-bottom:#e6e6e6;
  --footer:#161616;
  --white:#fff;
}
*{box-sizing:border-box;margin:0;padding:0}
html,body{width:910px;height:1200px;overflow:hidden;background:var(--white)}
body{font-family:"Lato",sans-serif;color:var(--ink);position:relative}
.wrap{width:762px;margin:0 auto;position:relative}

.topbar{height:39px;border-bottom:1px solid var(--line);background:#fafafa}
.topbar .wrap{display:flex;height:38px;align-items:center}
.contact-item{height:38px;display:flex;align-items:center;gap:7px;padding:0 22px 0 14px;border-left:1px solid var(--line);font-size:10.5px;color:#444}
.contact-item:last-of-type{border-right:1px solid var(--line)}
.contact-item svg{width:9px;height:9px;fill:#555}
.social{margin-left:auto;display:flex;gap:3px}
.social span{width:25px;height:25px;border:1.5px solid #bbb;border-radius:50%}

.header{height:58px}
.header .wrap{display:flex;align-items:center;height:58px}
.brand{font-family:"Roboto Condensed",sans-serif;font-size:29px;color:var(--sky);font-weight:400}
.search{margin-left:auto;width:134px;height:32px;border:1px solid #ccc;position:relative}
.search svg{position:absolute;right:7px;top:8px;width:14px;height:14px}

.nav{height:40px;background:linear-gradient(var(--sky),#34a4ef)}
.nav .wrap{display:flex;height:40px;align-items:center;gap:31px}
.nav a{font-family:"Roboto Condensed",sans-serif;font-size:11.5px;color:var(--white);text-decoration:none}
.nav a.current{color:#0a2a4a}

.slider{height:291px;position:relative}
.slide-art{position:absolute;left:140px;top:40px;width:625px;height:200px;background:radial-gradient(ellipse at center,#d9d9d9 0%,#f1f1f1 45%,#fff 75%)}
.slide-next{position:absolute;right:37px;top:130px}

.welcome{height:242px;background:linear-gradient(var(--sky),var(--blue-deep));color:var(--white);text-align:center;padding-top:25px}
.welcome h1{font-family:"Roboto Condensed",sans-serif;font-weight:400;font-size:24px;margin-bottom:14px}
.welcome p{font-size:10.7px;line-height:24px;width:762px;margin:0 auto 23px}

.results{height:312px;background:linear-gradient(var(--panel-top),var(--panel-bottom))}
.results .wrap{display:flex;height:312px}
.col-results{width:476px;border-right:1px solid #ddd;padding-top:22px}
.col-news{padding:22px 0 0 47px;flex:1}
h2.section{font-family:"Roboto Condensed",sans-serif;font-weight:400;font-size:13px;color:var(--link);margin-bottom:12px}
.checks{list-style:none}
.checks li{display:flex;gap:8px;font-size:10.3px;line-height:19px;color:var(--muted);margin-bottom:19px;width:414px}
.checks svg{flex:0 0 18px;height:18px}
.news{display:flex;gap:14px;margin-bottom:30px}
.date{flex:0 0 31px;width:31px;text-align:center}
.date b{display:block;width:31px;height:33px;border:1px solid #ddd;background:var(--white);font-family:"Roboto Condensed",sans-serif;font-size:12.5px;line-height:31px;color:#444}
.date span{display:block;font-size:8px;margin-top:7px;color:#444}
.news h3{font-family:"Roboto Condensed",sans-serif;font-weight:400;font-size:13px;color:#444}
.news .meta{font-size:8.5px;color:var(--faint);margin:4px 0 8px}
.news p{font-size:10.3px;line-height:19px;color:var(--muted)}

.membership{height:144px}
.membership h2{padding-top:18px}
.badges{display:flex;align-items:center;gap:36px;padding-left:36px;margin-top:18px}
.badge{height:48px;border-radius:3px}
.b1{width:192px;background:linear-gradient(90deg,#2f6fa8,#5a8fbf)}
.b2{width:218px;background:linear-gradient(90deg,#5b9ed6,#cfe2f2)}
.b3{width:208px;background:linear-gradient(90deg,#3a3a3a,#888)}

.footer{height:74px;background:var(--footer);color:#8a8a8a;font-size:8.8px;text-align:center;line-height:74px}
</style>
</head>
<body>
<div class="topbar"><div class="wrap">
  <div class="contact-item"><svg viewBox="0 0 10 10"><path d="M2 0.5 3.6 2.4 2.7 3.5c.6 1.5 2.2 3.1 3.7 3.7l1.1-.9L9.5 8 8 9.5C4 9.2.8 6 .5 2Z"/></svg>(555) 318-2046</div>
  <div class="contact-item"><svg viewBox="0 0 10 10"><path d="M0 1.5h10v7H0Zm.8.8L5 5.5l4.2-3.2Z"/></svg>tovimar@mailpost.com</div>
  <div class="social"><span></span><span></span><span></span><span></span></div>
</div></div>

<header class="header"><div class="wrap">
  <div class="brand">Tovimarinc</div>
  <div class="search"><svg viewBox="0 0 14 14"><circle cx="5.5" cy="5.5" r="4.2" fill="none" stroke="#444" stroke-width="1.6"/><path d="M8.6 8.6 13 13" stroke="#444" stroke-width="2"/></svg></div>
</div></header>

<nav class="nav"><div class="wrap">
  <a class="current" href="#">Home</a><a href="#">Our Company</a><a href="#">Housing Rehap Application</a><a href="#">Affordable Application</a><a href="#">Contact us</a>
</div></nav>

<section class="slider">
  <div class="slide-art" role="img" aria-label="Colourful word cloud around the word COMMUNITY with planning and leadership terms"></div>
  <svg class="slide-next" width="30" height="30" viewBox="0 0 30 30"><circle cx="15" cy="15" r="13.5" fill="none" stroke="var(--blue)" stroke-width="1.8"/><path d="M12.5 8.5 19 15l-6.5 6.5" fill="none" stroke="var(--blue)" stroke-width="1.8"/></svg>
</section>

<section class="welcome">
  <h1>Welcome To Tovimar,inc</h1>
  <p>Tovimar, Inc. is a city planning firm that specializes in community development and housing rehabilitation program planning, design and implementation. We have over twenty years of experience in developing and administering income base-base housing and programs in accordance with National Bureau of Residential Renewal (NBRR) and State Board on Fair Community Housing (SBFH) rules and regulations,</p>
  <p>In addition, our firm is capable of providing the technical and administrative assistance our clients require for implementation of their income based housing programs. H. Walden Pryor Associates is one of the most experience urban planning firms in New Jersey, with over forty years of as consulting planners.</p>
</section>

<section class="results"><div class="wrap">
  <div class="col-results">
    <h2 class="section">WE GET RESULTS:</h2>
    <ul class="checks">
      <li><svg viewBox="0 0 18 18"><circle cx="9" cy="9" r="9" fill="#c9c9c9"/><path d="M5 9.3 8 12l5-6" fill="none" stroke="#fff" stroke-width="2"/></svg><span>Tovimar designs income based programs to be supported by federal placement lotteries state funding.</span></li>
      <li><svg viewBox="0 0 18 18"><circle cx="9" cy="9" r="9" fill="#c9c9c9"/><path d="M5 9.3 8 12l5-6" fill="none" stroke="#fff" stroke-width="2"/></svg><span>We implement local programs to benefit people seeking access to affordable housing.</span></li>
      <li><svg viewBox="0 0 18 18"><circle cx="9" cy="9" r="9" fill="#c9c9c9"/><path d="M5 9.3 8 12l5-6" fill="none" stroke="#fff" stroke-width="2"/></svg><span>Our experienced staff screen applicants for local affordable housing.</span></li>
      <li><svg viewBox="0 0 18 18"><circle cx="9" cy="9" r="9" fill="#c9c9c9"/><path d="M5 9.3 8 12l5-6" fill="none" stroke="#fff" stroke-width="2"/></svg><span>We pre-qualify persons who have applied for housing rehabilitation.<br>Conduct placement lotteries</span></li>
      <li><svg viewBox="0 0 18 18"><circle cx="9" cy="9" r="9" fill="#c9c9c9"/><path d="M5 9.3 8 12l5-6" fill="none" stroke="#fff" stroke-width="2"/></svg><span>Through local housing rehabilitation programs, our experience construction inspectors determine what improvements are required at eligible units based on local building codes and health and safety issues.</span></li>
    </ul>
  </div>
  <div class="col-news">
    <h2 class="section">Latest News</h2>
    <article class="news"><div class="date"><b>24</b><span>MAR</span></div><div><h3>Money Back Guarantee!</h3><div class="meta">No Comments</div><p>Lorem ipsum dolor sit amet, consectetur adipisicing elit, sed do eiusmod tempor incididunt ut labore et dolore magna aliqua.</p></div></article>
    <article class="news"><div class="date"><b>24</b><span>MAR</span></div><div><h3>Money Back Guarantee!</h3><div class="meta">No Comments</div><p>Lorem ipsum dolor sit amet, consectetur adipisicing elit, sed do eiusmod tempor incididunt ut labore et dolore magna aliqua.</p></div></article>
  </div>
</div></section>

<section class="membership"><div class="wrap">
  <h2 class="section">Membership</h2>
  <div class="badges">
    <div class="badge b1" role="img" aria-label="Member association badge"></div>
    <div class="badge b2" role="img" aria-label="Member association badge"></div>
    <div class="badge b3" role="img" aria-label="Member association badge"></div>
  </div>
</div></section>

<footer class="footer">Copy Right 2014 Tovimar, 215 Harbor Crest Road, Lakeview, New Jersey, 08700 &nbsp;TEL (555) 318-2046 Fax (555) 318-2047</footer>
</body>
</html>
```